Business card for marketing analytics company

Need a business card for new company. I have a logo already that I want to be built into the card and should use those colours

Company is called steered by tallies
Design must bring steered by tallies to life not be a card that could be for anyone with a logo put on it.

Like the front to be fairly clean and uncluttered bringing the logo out with a suitable design on the back of the card.

The logo represents a compass and business growth so those themes along with numbers, analytics , data are appropriate.
I'm often working with creative industries so also needs to reflect the creative side of analytics rather than be very corporate looking.

Target Market(s)

Ad agency, media agency, consumer goods clients

Industry/Entity Type

Market Research

Contact Information for Business Card

Needs to include name, title, email and phone number

Colors
f78f20
f68d4d
ec1f27

Requirements
Must have
• Must bring steered by tallies to life not be a card that could be for anyone with a logo put on it.
• Logo, Correct colours
• Like a design on the back that relates to company name
• Designs for both sides
Should not have
• Please do not just submit logo and a coloured card.
• It needs to have a design element to it
• No black background
• No clear cards - needs front & back

```html
<!DOCTYPE html>
<html lang="en">
<head>
<meta charset="utf-8">
<title>Steered by Tallies – Business Card</title>
<link rel="stylesheet" href="https://fonts.googleapis.com/css2?family=Open+Sans:wght@400;600;700&display=swap">
<style>
  :root {
    --stage: #e6e6e6;
    --paper: #ffffff;
    --orange: #f37422;
    --orange-bright: #f78f20;
    --red: #c41d24;
    --ink: #4a4f55;
    --divider: #c9c9c9;
    --white: #ffffff;
  }
  * { box-sizing: border-box; margin: 0; padding: 0; }
  html, body {
    width: 1200px;
    height: 987px;
    overflow: hidden;
    background: var(--stage);
    font-family: "Open Sans", Arial, sans-serif;
  }
  .canvas {
    position: relative;
    width: 1200px;
    height: 987px;
  }
  .card {
    position: absolute;
    width: 615px;
    height: 352px;
    overflow: hidden;
  }
  /* Front */
  .card-front {
    left: 293px;
    top: 130px;
    background: var(--paper);
  }
  .brand {
    position: absolute;
    left: 33px;
    top: 131px;
    display: flex;
    align-items: center;
    gap: 18px;
  }
  .brand-dot {
    width: 84px;
    height: 84px;
    border-radius: 50%;
    border: 3px solid var(--orange);
    flex: none;
  }
  .brand-name {
    color: var(--orange);
    font-weight: 600;
    font-size: 26px;
    line-height: 30px;
  }
  .divider {
    position: absolute;
    left: 319px;
    top: 108px;
    width: 1px;
    height: 132px;
    background: var(--divider);
  }
  .contact {
    position: absolute;
    left: 342px;
    top: 104px;
  }
  .person-name {
    color: var(--orange);
    font-weight: 700;
    font-size: 23px;
    line-height: 28px;
    letter-spacing: 0.2px;
  }
  .person-title {
    color: var(--red);
    font-size: 17px;
    line-height: 22px;
    margin-bottom: 10px;
  }
  .contact-list { list-style: none; }
  .contact-list li {
    display: flex;
    align-items: center;
    gap: 8px;
    color: var(--ink);
    font-size: 16px;
    line-height: 23.5px;
  }
  .contact-list svg { width: 15px; height: 15px; flex: none; }
  .footer-bands {
    position: absolute;
    left: 0;
    bottom: 0;
    width: 615px;
    height: 24px;
  }
  /* Back */
  .card-back {
    left: 292px;
    top: 505px;
    background: var(--orange);
  }
  .back-dot {
    position: absolute;
    left: 222px;
    top: 68px;
    width: 172px;
    height: 172px;
    border-radius: 50%;
    border: 5px solid var(--white);
  }
  .back-url {
    position: absolute;
    left: 0;
    top: 290px;
    width: 100%;
    text-align: center;
    color: var(--white);
    font-size: 16px;
    letter-spacing: 5.5px;
  }
</style>
</head>
<body>
<main class="canvas">
  <section class="card card-front" aria-label="Business card front">
    <div class="brand">
      <span class="brand-dot"></span>
      <span class="brand-name">Steered by<br>Tallies</span>
    </div>
    <span class="divider"></span>
    <div class="contact">
      <p class="person-name">DANIEL REYES</p>
      <p class="person-title">CEO/Founder</p>
      <ul class="contact-list">
        <li>
          <svg viewBox="0 0 16 16" aria-hidden="true"><path fill="var(--orange)" d="M3.6 1.2l2.3 2.6-1.3 1.8c.8 1.9 2.2 3.3 4.1 4.2l1.8-1.3 2.6 2.3-1.1 2.4C6.4 13 3 9.6 1.2 4.1z"/></svg>
          555 214 7730
        </li>
        <li>
          <svg viewBox="0 0 16 16" aria-hidden="true"><rect x="1" y="3.5" width="14" height="9" fill="var(--orange)"/><path d="M1.5 4l6.5 5 6.5-5" fill="none" stroke="#fff" stroke-width="1.3"/></svg>
          daniel@steeredbytallies.com
        </li>
        <li>
          <svg viewBox="0 0 16 16" aria-hidden="true"><circle cx="8" cy="8" r="7" fill="var(--orange)"/><path d="M4 5c2 0 2 2 3.5 2.5S8 10 6 12M10 3c0 2 2 2 3 3M10 13c0-2 1-3 3-3" fill="none" stroke="#fff" stroke-width="1.2"/></svg>
          www.steeredbytallies.com
        </li>
      </ul>
    </div>
    <svg class="footer-bands" viewBox="0 0 615 24" preserveAspectRatio="none" aria-hidden="true">
      <polygon points="0,0 404,0 398,24 0,24" fill="var(--orange)"/>
      <polygon points="409,0 615,0 615,24 403,24" fill="var(--red)"/>
    </svg>
  </section>

  <section class="card card-back" aria-label="Business card back">
    <span class="back-dot" role="img" aria-label="Steered by Tallies brand mark"></span>
    <p class="back-url">www.steeredbytallies.com</p>
  </section>
</main>
</body>
</html>
```